Poster for Stores

We need a poster design for my company, ourbrightvillage.net. The company is a social networking site oriented around the town.

I have a slogan for the site....Helping Town Connect with People.

I want the background color to be a type of green.

I want to have a picture of a generic town in the background.

I would some of the below text in the poster to be:

1) All your local town deals in one place.
2) its's free..no cost
3) create town events...create groups...blog or forum about/around the town.
4) find out about city/town services

```html
<!DOCTYPE html>
<html lang="en">
<head>
<meta charset="utf-8">
<title>Helping Town Connect with People – ourbrightvillage.net</title>
<link rel="stylesheet" href="https://fonts.googleapis.com/css2?family=Signika:wght@600;700&family=Arimo:wght@700&display=swap">
<style>
  :root {
    --paper: #ffffff;
    --ink: #111111;
    --headline: #ffffff;
    --teal: #5fb8a6;
    --mint: #a9dccb;
    --sea: #3f8f86;
    --plum: #8a4c78;
    --sun: #e8d24a;
    --sky: #d9ecef;
  }
  html, body {
    margin: 0;
    padding: 0;
    overflow: hidden;
    background: var(--paper);
  }
  .poster {
    position: relative;
    width: 845px;
    height: 1200px;
    overflow: hidden;
    background: var(--paper);
  }
  .town-artwork {
    position: absolute;
    left: 0;
    top: 0;
    width: 845px;
    height: 1024px;
    display: block;
  }
  .slogan {
    position: absolute;
    left: 438px;
    top: 222px;
    margin: 0;
    font-family: "Signika", sans-serif;
    font-weight: 700;
    font-size: 112px;
    line-height: 129px;
    letter-spacing: 1px;
    color: var(--headline);
  }
  .slogan span { display: block; }
  .site-name {
    position: absolute;
    left: 440px;
    top: 944px;
    margin: 0;
    font-family: "Signika", sans-serif;
    font-weight: 700;
    font-size: 38px;
    line-height: 1;
    color: var(--headline);
  }
  .features {
    position: absolute;
    left: 0;
    top: 1058px;
    width: 845px;
    margin: 0;
    padding: 0;
    list-style: none;
    text-align: center;
    font-family: "Arimo", sans-serif;
    font-weight: 700;
    font-size: 19px;
    line-height: 29px;
    color: var(--ink);
  }
</style>
</head>
<body>
<main class="poster">
  <svg class="town-artwork" viewBox="0 0 845 1024" role="img" aria-label="Colourful painted illustration of a generic town street with a yellow building, arched windows and a sunlit road in green, teal and plum tones">
    <defs>
      <linearGradient id="townWash" x1="0" y1="0" x2="1" y2="1">
        <stop offset="0" stop-color="var(--mint)"/>
        <stop offset="0.35" stop-color="var(--teal)"/>
        <stop offset="0.65" stop-color="var(--sea)"/>
        <stop offset="1" stop-color="var(--teal)"/>
      </linearGradient>
      <radialGradient id="plumGlow" cx="0.75" cy="0.1" r="0.45">
        <stop offset="0" stop-color="var(--plum)" stop-opacity="0.55"/>
        <stop offset="1" stop-color="var(--plum)" stop-opacity="0"/>
      </radialGradient>
      <radialGradient id="sunGlow" cx="0.3" cy="0.65" r="0.4">
        <stop offset="0" stop-color="var(--sun)" stop-opacity="0.5"/>
        <stop offset="1" stop-color="var(--sun)" stop-opacity="0"/>
      </radialGradient>
    </defs>
    <rect width="845" height="1024" fill="url(#townWash)"/>
    <rect width="845" height="1024" fill="url(#plumGlow)"/>
    <rect width="845" height="1024" fill="url(#sunGlow)"/>
  </svg>

  <h1 class="slogan">
    <span>Helping</span>
    <span>Town</span>
    <span>Connect</span>
    <span>with</span>
    <span>People</span>
  </h1>
  <p class="site-name">ourbrightvillage.net</p>

  <ul class="features">
    <li>All your local town deals in one place</li>
    <li>It's free..no cost</li>
    <li>Create town events...create groups...blog or forum around the town</li>
    <li>Find out about town services</li>
  </ul>
</main>
</body>
</html>
```